The design should look similar to the uploaded example to accommodate the information needed for a business card template. I would like to see the colors orange and charcoal grey incorporated along with the logo.The following should be on the back of the card SPECIALIZING IN NEW AND USED TIRES & WHEELS FOR:- Loaders- Skid Steers- Telehandlers- Boom Lifts- Forklifs and moreELIMINATING DOWNTIMEWheel Exchange Program for New & Used Foam Filled and Solid Rubber TiresSPECIALTY SERVICES- Foam Filling Tires- Largest Tire Press in SE- ONSITE Forklift Tire Press- Boom Truck Services - Rubber Tracks

Target Market(s)

New and Existing Customers

Industry/Entity Type

Business

Contact Information for Business Card

NAMEHEAVY DUTY TIRE, LLC8470 Belvedere RoadWest Palm Beach, FL 33411P: 844-HD-TIRESF: 561-431-6469C:E: W: WWW.GRANITERIMSUPPLY-EXAMPLE.COM

Font styles to use
Sans Serif

Colors
f37122
333333

Requirements
Must have
• The logo and the information indicated for the backside of the card
Nice to have
• Keep the orange and charcoal grey colors

```html
<!DOCTYPE html>
<html lang="en">
<head>
<meta charset="utf-8">
<title>Granite Rim Supply – Business Card</title>
<link rel="stylesheet" href="https://fonts.googleapis.com/css2?family=Source+Sans+3:wght@400;600;700&display=swap">
<style>
  :root {
    --orange: #f37122;
    --orange-card: #f7843a;
    --charcoal: #333333;
    --white: #ffffff;
    --page: #ececec;
  }
  * { margin: 0; padding: 0; box-sizing: border-box; }
  html, body { width: 1200px; height: 900px; overflow: hidden; }
  body {
    background: var(--page);
    font-family: "Source Sans 3", Arial, sans-serif;
    position: relative;
  }
  .card {
    position: absolute;
    width: 540px;
    height: 310px;
    box-shadow: 0 6px 18px rgba(0,0,0,0.18);
    overflow: hidden;
  }
  /* Back side */
  .card-back {
    left: 40px; top: 150px;
    background: var(--orange-card);
    color: var(--white);
    padding: 40px 36px;
  }
  .back-mark {
    position: absolute;
    left: 150px; top: 60px;
    font-size: 96px;
    line-height: 0.9;
    font-weight: 700;
    color: rgba(255,255,255,0.08);
    text-align: center;
    pointer-events: none;
  }
  .back-heading {
    position: relative;
    font-size: 15px;
    font-weight: 600;
    text-transform: uppercase;
    letter-spacing: 0.3px;
  }
  .back-heading.large { font-size: 19px; font-weight: 700; }
  .back-list {
    position: relative;
    list-style: none;
    font-size: 14px;
    font-weight: 600;
    line-height: 1.35;
    margin-top: 4px;
  }
  .back-list li { display: inline; }
  .back-list li + li::before { content: "•"; margin: 0 10px; }
  .back-list li.newline::before { content: ""; margin: 0; }
  .back-list li.newline { display: block; }
  .back-section { margin-top: 22px; }
  .back-section.tight { margin-top: 14px; }
  .back-text {
    position: relative;
    font-size: 14px;
    font-weight: 600;
    line-height: 1.3;
  }
  /* Front side */
  .card-front {
    left: 620px; top: 440px;
    background: var(--white);
  }
  .brand {
    position: absolute;
    left: 36px; top: 120px;
    display: flex;
    align-items: center;
    gap: 12px;
  }
  .brand-dot {
    width: 34px; height: 34px;
    border-radius: 50%;
    background: var(--orange);
  }
  .brand-name {
    font-size: 30px;
    font-weight: 700;
    color: var(--charcoal);
    line-height: 1;
  }
  .contact {
    position: absolute;
    left: 300px; top: 40px;
    color: var(--charcoal);
  }
  .contact-name { color: var(--orange); font-size: 18px; font-weight: 600; }
  .contact-company { color: var(--orange); font-size: 14px; font-weight: 600; margin-top: 2px; }
  .contact-address { font-size: 13px; line-height: 1.35; margin-top: 6px; }
  .contact-lines { list-style: none; margin-top: 12px; font-size: 13px; line-height: 1.6; }
  .contact-lines li { display: flex; align-items: center; gap: 10px; }
  .contact-lines svg { width: 11px; height: 11px; fill: var(--orange); flex: none; }
</style>
</head>
<body>
  <section class="card card-back" aria-label="Card back">
    <div class="back-mark" aria-hidden="true">GRANITE<br>RIM</div>
    <h2 class="back-heading">Specializing in new and used tires &amp; wheels for:</h2>
    <ul class="back-list">
      <li>Loaders</li><li>Skid Steers</li><li>Telehandlers</li><li>Boom Lifts</li>
      <li class="newline">Forklifs and more</li>
    </ul>
    <div class="back-section">
      <h3 class="back-heading">Eliminating Downtime</h3>
      <p class="back-text">Wheel Exchange Program for New &amp; Used Foam<br>Filled and Solid Rubber Tires</p>
    </div>
    <div class="back-section tight">
      <h2 class="back-heading large">Specialty Services</h2>
      <ul class="back-list">
        <li>Foam Filling Tires</li><li>Largest Tire Press in SE</li>
        <li class="newline">ONSITE Forklift Tire Press</li>
      </ul>
      <ul class="back-list">
        <li>Boom Truck Services</li><li>Rubber Tracks</li>
      </ul>
    </div>
  </section>

  <section class="card card-front" aria-label="Card front">
    <div class="brand">
      <span class="brand-dot"></span>
      <span class="brand-name">GRANITE RIM</span>
    </div>
    <div class="contact">
      <p class="contact-name">Marcus Delgado</p>
      <p class="contact-company">GRANITE RIM SUPPLY, LLC</p>
      <p class="contact-address">5126 Marston Lane<br>West Palm Beach, FL 33411</p>
      <ul class="contact-lines">
        <li><svg viewBox="0 0 12 12"><path d="M2.5 1l2 2.2-1 1.3a7 7 0 0 0 4 4l1.3-1 2.2 2-1.3 1.5C5.5 11 1 6.5 1 2.3z"/></svg>844-GR-WHEEL</li>
        <li><svg viewBox="0 0 12 12"><rect x="3" y="1" width="6" height="3"/><rect x="1" y="4" width="10" height="7" rx="1"/></svg>561-278-9053</li>
        <li><svg viewBox="0 0 12 12"><path d="M3 0h6a1 1 0 0 1 1 1v10a1 1 0 0 1-1 1H3a1 1 0 0 1-1-1V1a1 1 0 0 1 1-1zm0 2v7h6V2z"/></svg>123-456-7890</li>
        <li><svg viewBox="0 0 12 12"><path d="M0 2h12v1L6 7 0 3zm0 2.5l6 4 6-4V10H0z"/></svg>info@graniterimsupply-example.com</li>
        <li><svg viewBox="0 0 12 12"><circle cx="6" cy="6" r="6"/></svg>www.graniterimsupply-example.com</li>
      </ul>
    </div>
  </section>
</body>
</html>
```